Stylish Business Cards Wanted

- DOUBLE SIDED Design Required -

High end, edgy cards for a corporate and personal stylist. Must include logo,
Name: Belinda Harwick
Title: Director and Stylist
telephone : +61 8 7142 5809
email: belinda@theloombriefing.example
website: theloombriefing.example
Tag: Corporate Workwear & Uniform Specialist | Personal Stylist
Would like nice icons for telephone, email, website

Target Market(s)

Businesses wanting stylish uniforms, people wanting stylish wardrobes

Industry/Entity Type

Corporate Workwear Stylist

Contact Information for Business Card

I would like black, white and gold foiling incorporated in the design - possibly a touch of the other colours on my branding guide attached Name: Belinda Harwick Title: Director and Stylist telephone : +61 8 7142 5809 email: belinda@theloombriefing.example website: theloombriefing.example Tag: Corporate Workwear & Uniform Specialist | Personal Stylist Would like nice icons for telephone, email, website

Font styles to use
Other font styles liked:
• Raleway

Colors

Designer to choose colors to be used in the design.

Requirements
Must have
• Gold foil accents

```html
<!DOCTYPE html>
<html lang="en">
<head>
<meta charset="utf-8">
<title>The Loom Briefing — Business Cards</title>
<link rel="stylesheet" href="https://fonts.googleapis.com/css2?family=Raleway:wght@600&family=Roboto:wght@400&family=Dancing+Script:wght@500&display=swap">
<style>
  :root {
    --navy: #141b2e;
    --gold: #e0b042;
    --white: #fbfbf9;
    --ink: #1c2233;
    --stage: #cfcfcf;
  }
  * { box-sizing: border-box; margin: 0; padding: 0; }
  html, body { width: 1200px; height: 852px; overflow: hidden; }
  body {
    background: var(--stage);
    position: relative;
    font-family: "Roboto", Arial, sans-serif;
  }
  .card {
    position: absolute;
    width: 520px;
    height: 300px;
    border-radius: 22px;
    overflow: hidden;
  }
  .card--front { left: 50px; top: 276px; background: var(--navy); }
  .card--back  { left: 630px; top: 276px; background: var(--white); }

  .brand {
    position: absolute;
    font-family: "Raleway", Arial, sans-serif;
    font-weight: 600;
    text-align: center;
    line-height: 1.1;
  }
  .card--front .brand {
    left: 0; right: 0; top: 108px;
    color: var(--gold);
    font-size: 38px;
    letter-spacing: 1px;
  }
  .card--back .brand {
    left: 20px; top: 112px; width: 190px;
    color: var(--white);
    font-size: 26px;
  }

  .card__shapes { position: absolute; inset: 0; }

  .contact {
    position: absolute;
    left: 300px; top: 52px;
    color: var(--ink);
  }
  .contact__name {
    font-family: "Dancing Script", cursive;
    font-weight: 500;
    color: var(--gold);
    font-size: 26px;
    line-height: 1;
    white-space: nowrap;
  }
  .contact__title { font-size: 11.5px; margin-top: 6px; }
  .contact__list { list-style: none; margin-top: 16px; }
  .contact__item {
    display: flex; align-items: center; gap: 8px;
    font-size: 11px; line-height: 19px;
    white-space: nowrap;
  }
  .contact__icon { width: 11px; height: 11px; flex: none; }

  .tagline {
    position: absolute;
    left: 244px; right: 12px; top: 236px;
    height: 26px;
    display: flex; align-items: center; justify-content: space-between;
    font-family: "Dancing Script", cursive;
    font-weight: 500;
    font-size: 10.5px;
    color: var(--navy);
    white-space: nowrap;
  }
</style>
</head>
<body>

  <section class="card card--front" aria-label="Business card front">
    <p class="brand">The Loom<br>Briefing</p>
  </section>

  <section class="card card--back" aria-label="Business card back">
    <svg class="card__shapes" viewBox="0 0 520 300" aria-hidden="true">
      <path d="M0 0 H150 C235 55 282 160 296 300 H0 Z" fill="var(--navy)"/>
      <path d="M150 0 C235 55 282 160 296 300" fill="none" stroke="var(--gold)" stroke-width="7"/>
      <path d="M226 236 H520 V262 H240 Z" fill="var(--gold)"/>
    </svg>

    <p class="brand">The Loom<br>Briefing</p>

    <div class="contact">
      <p class="contact__name">Belinda Harwick</p>
      <p class="contact__title">Director and Stylist</p>
      <ul class="contact__list">
        <li class="contact__item">
          <svg class="contact__icon" viewBox="0 0 12 12" aria-hidden="true">
            <circle cx="6" cy="6" r="5.3" fill="none" stroke="var(--gold)" stroke-width="1"/>
            <path d="M4 3.3 L5 4.8 L4.5 5.4 Q5.4 6.9 6.6 7.5 L7.2 7 L8.7 8 L8 8.8 Q5.6 8.6 3.4 4.2 Z" fill="var(--gold)"/>
          </svg>
          +61 8 7142 5809
        </li>
        <li class="contact__item">
          <svg class="contact__icon" viewBox="0 0 12 12" aria-hidden="true">
            <rect x="1" y="2.5" width="10" height="7" fill="none" stroke="var(--gold)" stroke-width="1"/>
            <path d="M1 2.5 L6 6.5 L11 2.5" fill="none" stroke="var(--gold)" stroke-width="1"/>
          </svg>
          belinda@theloombriefing.example
        </li>
        <li class="contact__item">
          <svg class="contact__icon" viewBox="0 0 12 12" aria-hidden="true">
            <circle cx="6" cy="6" r="5.3" fill="var(--gold)"/>
            <path d="M0.7 6 H11.3 M6 0.7 Q3 6 6 11.3 M6 0.7 Q9 6 6 11.3" fill="none" stroke="var(--white)" stroke-width="0.8"/>
          </svg>
          www.theloombriefing.example
        </li>
      </ul>
    </div>

    <p class="tagline">
      <span>Corporate Workwear &amp; Uniform Specialist</span>
      <span>Personal Stylist</span>
    </p>
  </section>

</body>
</html>
```